Business Card Design

We like to use greens as you will see in our logo (but not TOO much green). We are a Dental Clinic in a somewhat eccentric community. We do not like the dated sharp designs which we see many dentists use. We're looking for something bright and fresh while still maintaining the integrity of the profession. Elegance is not necessarily what we are going for... we need for the design to be "mature" but also up-lifting.

See our logo.
Updates

Project Deadline Extended
Reason: We have 5 designs which we like. But we'd like to see a few more before committing to a design.

Project Deadline Extended
Reason: We are awaiting revisions to this project. We are still welcoming designs while we wait to see if designers are able to provide to us the revisions we require in order to proceed with a selection.

Target Market(s)

Younger families - ages late 20's to early 40's

Industry/Entity Type

Business

Contact Information for Business Card

Corwel T. Banfry DDS 2730 W. Halvert Rd. Ste. 7 Royal Oak, MI 48391 (248)555-0174 FX (248)555-0189 info@BrightwellDentalCareMi.com BrigthwellDentalCareMi.com on the back of the card we need an appointment reminder (For____ Date___ Time____) with "If you are unable to keep your appointment, kindly give 48 hours notice" at the bottom. No use of teeth in the design. DOUBLE SIDED DESIGN

Requirements
Should not have
• The use of pictures of teeth

```html
<!DOCTYPE html>
<html lang="en">
<head>
<meta charset="utf-8">
<title>Brightwell Dental Care – Business Card</title>
<link rel="stylesheet" href="https://fonts.googleapis.com/css2?family=PT+Sans:wght@400;700&family=Tinos:ital,wght@0,400;0,700;1,400&display=swap">
<style>
  :root {
    --lime: #8cc63f;
    --forest: #2f7d1f;
    --ink: #333333;
    --muted: #555555;
    --paper: #ffffff;
    --stage: #e9e6e1;
    --rule: #777777;
  }
  * { box-sizing: border-box; margin: 0; padding: 0; }
  html, body {
    width: 1200px; height: 492px; overflow: hidden;
    background: var(--stage);
    font-family: "PT Sans", sans-serif;
    color: var(--ink);
  }
  .stage { position: relative; width: 1200px; height: 492px; }

  .card {
    position: absolute; top: 96px;
    width: 500px; height: 300px;
    background: var(--paper);
    box-shadow: 0 6px 18px rgba(0,0,0,.18);
    overflow: hidden;
  }
  .card--front { left: 60px; }
  .card--back  { left: 640px; }

  /* front */
  .front-band { position: absolute; inset: 0; }
  .doctor-name {
    position: absolute; top: 22px; left: 0; width: 100%;
    text-align: center; color: var(--paper);
    font-size: 21px; letter-spacing: .3px;
  }
  .doctor-name small { font-size: 15px; }

  .brand {
    position: absolute; display: flex; align-items: center; gap: 8px;
    color: var(--forest); font-weight: 700;
  }
  .brand__dot {
    width: 22px; height: 22px; border-radius: 50%; background: var(--lime);
    flex: none;
  }
  .card--front .brand { top: 168px; left: 0; width: 100%; justify-content: center; font-size: 27px; }

  .contact {
    position: absolute; top: 222px; left: 0; width: 100%;
    display: flex; font-size: 13px; color: var(--ink);
  }
  .contact__address {
    width: 262px; text-align: right; padding-right: 14px;
    align-self: center; line-height: 1.35; margin-top: 28px;
  }
  .contact__divider { width: 1px; background: var(--ink); height: 74px; }
  .contact__list { list-style: none; padding-left: 10px; line-height: 1.45; }
  .contact__list li { display: flex; align-items: center; gap: 5px; }
  .contact__list svg { width: 11px; height: 11px; flex: none; }

  /* back */
  .card--back .brand { top: 26px; right: 24px; font-size: 21px; }
  .appointment-title {
    position: absolute; top: 78px; left: 30px;
    font-family: "Tinos", serif; font-weight: 700;
    color: var(--forest); font-size: 16px; letter-spacing: .4px;
  }
  .title-rule {
    position: absolute; top: 98px; left: 200px; width: 260px;
    border-top: 1px dotted var(--rule);
  }
  .form-row {
    position: absolute; left: 30px; display: flex; align-items: flex-end;
    font-size: 14px; color: var(--muted);
  }
  .fill-line { border-bottom: 1px dotted var(--rule); height: 1px; margin: 0 6px 4px; }
  .fill-line--solid { border-bottom-style: solid; }
  .field-box {
    width: 88px; height: 20px; border: 1px solid var(--rule); border-radius: 3px;
  }
  .row-name { top: 124px; }
  .row-date { top: 152px; }
  .row-next { top: 186px; }
  .row-days { top: 222px; font-weight: 700; font-size: 14px; gap: 6px; align-items: center; }
  .day-box {
    width: 30px; height: 20px; border: 1px solid var(--rule); border-radius: 3px;
    margin-right: 6px;
  }
  .notice {
    position: absolute; top: 262px; left: 30px; right: 20px;
    font-family: "Tinos", serif; font-style: italic;
    font-size: 14px; color: var(--muted);
  }
</style>
</head>
<body>
<main class="stage">

  <section class="card card--front" aria-label="Business card front">
    <svg class="front-band" width="500" height="300" viewBox="0 0 500 300" aria-hidden="true">
      <path d="M0 0 H500 V82 Q250 40 0 140 Z" fill="var(--lime)"/>
      <path d="M0 158 Q250 52 500 96" fill="none" stroke="var(--forest)" stroke-width="8"/>
    </svg>
    <h1 class="doctor-name">Corwel T. Banfry, <small>DDS</small></h1>

    <div class="brand"><span class="brand__dot"></span>Brightwell Dental Care</div>

    <div class="contact">
      <p class="contact__address">2730 W. Halvert Rd. Ste. 7<br>Royal Oak, MI 48391</p>
      <span class="contact__divider"></span>
      <ul class="contact__list">
        <li>
          <svg viewBox="0 0 12 12"><circle cx="6" cy="6" r="5.5" fill="none" stroke="var(--ink)"/><path d="M4 3.2 L5 4.6 L4.4 5.3 Q5.2 6.8 6.7 7.6 L7.4 7 L8.8 8 L8 9 Q5 8.6 3 4 Z" fill="var(--ink)"/></svg>
          (248)555-0174
        </li>
        <li>
          <svg viewBox="0 0 12 12"><rect x="3" y="1" width="6" height="4" fill="var(--ink)"/><rect x="1" y="5" width="10" height="5" rx="1" fill="var(--ink)"/><rect x="3" y="7" width="6" height="4" fill="var(--paper)" stroke="var(--ink)" stroke-width=".8"/></svg>
          FX (248)555-0189
        </li>
        <li>
          <svg viewBox="0 0 12 12"><rect x="1" y="3" width="10" height="7" rx="1" fill="var(--ink)"/><path d="M1.5 3.5 L6 7 L10.5 3.5" fill="none" stroke="var(--paper)" stroke-width=".9"/></svg>
          info@BrightwellDentalCareMi.com
        </li>
        <li>
          <svg viewBox="0 0 12 12"><circle cx="6" cy="6" r="5" fill="none" stroke="var(--ink)"/><ellipse cx="6" cy="6" rx="2.2" ry="5" fill="none" stroke="var(--ink)" stroke-width=".8"/><path d="M1 6 H11 M2 3.5 H10 M2 8.5 H10" stroke="var(--ink)" stroke-width=".8"/></svg>
          www.BrigthwellDentalCareMi.com
        </li>
      </ul>
    </div>
  </section>

  <section class="card card--back" aria-label="Appointment reminder card back">
    <div class="brand"><span class="brand__dot"></span>Brightwell Dental Care</div>

    <h2 class="appointment-title">YOUR APPOINTMENT</h2>
    <span class="title-rule"></span>

    <div class="form-row row-name">Name :<span class="fill-line" style="width:300px"></span></div>
    <div class="form-row row-date">
      Date :<span class="fill-line fill-line--solid" style="width:92px"></span>
      <span style="margin-left:10px">Time :</span><span class="fill-line fill-line--solid" style="width:84px;margin-right:2px"></span>am / pm
    </div>
    <div class="form-row row-next">
      Next Appointment<span class="field-box" style="margin-left:10px"></span>
      <span class="field-box" style="margin-left:30px"></span>
    </div>
    <div class="form-row row-days">
      MON<span class="day-box"></span>TUE<span class="day-box"></span>WED<span class="day-box"></span>THU<span class="day-box"></span>FRI<span class="day-box"></span>SAT<span class="day-box"></span>
    </div>

    <p class="notice">If you are unable to keep your appointment, kindly give 48 hours notice</p>
  </section>

</main>
</body>
</html>
```